Business card for medical clinic

I need an upmarket, modern medical/health business card for my clinic

Contact Information for Business Card

name, address, email, qr code

```html
<!DOCTYPE html>
<html lang="en">
<head>
<meta charset="utf-8">
<title>Meridale Health Clinic – Business Card</title>
<link rel="stylesheet" href="https://fonts.googleapis.com/css2?family=EB+Garamond:wght@400;500&display=swap">
<style>
  :root {
    --backdrop: #2a2b2d;
    --card-top: #1f2533;
    --card-bottom: #141923;
    --brand-steel: #6f7c8f;
    --brand-blue: #2b95dc;
    --text-light: #d9dde4;
    --text-soft: #aeb5c0;
    --icon: #c8ced8;
  }
  * { box-sizing: border-box; margin: 0; padding: 0; }
  html, body {
    width: 1200px;
    height: 852px;
    overflow: hidden;
    background: var(--backdrop);
    font-family: "EB Garamond", Georgia, serif;
  }
  .sheet {
    position: relative;
    width: 1200px;
    height: 852px;
  }
  .card {
    position: absolute;
    width: 520px;
    height: 298px;
    border-radius: 22px;
    background: linear-gradient(160deg, var(--card-top), var(--card-bottom));
    box-shadow: 0 14px 30px rgba(0, 0, 0, 0.45);
    overflow: hidden;
  }
  .card--front { left: 110px; top: 120px; }
  .card--back { left: 570px; top: 432px; }

  /* Front */
  .front-brand {
    position: absolute;
    inset: 0;
    display: flex;
    flex-direction: column;
    align-items: center;
    justify-content: center;
    color: var(--brand-steel);
    font-weight: 500;
    text-transform: uppercase;
  }
  .front-brand__name {
    font-size: 40px;
    letter-spacing: 3px;
    line-height: 1;
  }
  .front-brand__sub {
    margin-top: 10px;
    font-size: 17px;
    letter-spacing: 9px;
    line-height: 1;
  }

  /* Back */
  .back-brand {
    position: absolute;
    left: 38px;
    top: 120px;
    display: flex;
    align-items: center;
    gap: 10px;
    color: var(--brand-blue);
    font-weight: 500;
    text-transform: uppercase;
  }
  .back-brand__dot {
    width: 14px;
    height: 14px;
    border-radius: 50%;
    background: var(--brand-blue);
    flex: none;
  }
  .back-brand__text { display: flex; flex-direction: column; }
  .back-brand__name { font-size: 19px; letter-spacing: 1.5px; line-height: 1; }
  .back-brand__sub { font-size: 10px; letter-spacing: 5px; margin-top: 4px; line-height: 1; }

  .contact {
    position: absolute;
    left: 292px;
    top: 62px;
    color: var(--text-light);
  }
  .contact__name {
    font-size: 21px;
    font-weight: 500;
    letter-spacing: 1px;
    color: var(--brand-blue);
    text-transform: uppercase;
    line-height: 1;
  }
  .contact__role {
    font-size: 14px;
    color: var(--text-soft);
    margin-top: 3px;
  }
  .contact__list {
    list-style: none;
    margin-top: 20px;
    font-size: 14px;
    line-height: 1;
  }
  .contact__item {
    display: flex;
    align-items: center;
    gap: 10px;
    margin-bottom: 8px;
  }
  .contact__icon {
    width: 11px;
    height: 11px;
    fill: var(--icon);
    flex: none;
  }
  .contact__address {
    margin-top: 6px;
    font-size: 15px;
  }
</style>
</head>
<body>
<main class="sheet">

  <section class="card card--front" aria-label="Card front">
    <div class="front-brand">
      <span class="front-brand__name">Meridale Health</span>
      <span class="front-brand__sub">Clinic</span>
    </div>
  </section>

  <section class="card card--back" aria-label="Card back">
    <div class="back-brand">
      <span class="back-brand__dot"></span>
      <span class="back-brand__text">
        <span class="back-brand__name">Meridale Health</span>
        <span class="back-brand__sub">Clinic</span>
      </span>
    </div>

    <div class="contact">
      <p class="contact__name">Daniel Hartwell</p>
      <p class="contact__role">Managing Director</p>
      <ul class="contact__list">
        <li class="contact__item">
          <svg class="contact__icon" viewBox="0 0 24 24" aria-hidden="true"><path d="M6.6 10.8a15.1 15.1 0 0 0 6.6 6.6l2.2-2.2a1 1 0 0 1 1-.25 11.4 11.4 0 0 0 3.6.57 1 1 0 0 1 1 1V20a1 1 0 0 1-1 1A17 17 0 0 1 3 4a1 1 0 0 1 1-1h3.5a1 1 0 0 1 1 1c0 1.25.2 2.45.57 3.6a1 1 0 0 1-.25 1z"/></svg>
          <span>0700-555-01234</span>
        </li>
        <li class="contact__item">
          <svg class="contact__icon" viewBox="0 0 24 24" aria-hidden="true"><path d="M2 5h20v14H2z M3.5 6.5 12 13l8.5-6.5" fill="none" stroke="#c8ced8" stroke-width="2.2"/></svg>
          <span>hello@meridaleclinic.com</span>
        </li>
        <li class="contact__item">
          <svg class="contact__icon" viewBox="0 0 24 24" aria-hidden="true"><circle cx="12" cy="12" r="9.5" fill="none" stroke="#c8ced8" stroke-width="2"/><path d="M2.5 12h19M12 2.5c3 3 3 16 0 19M12 2.5c-3 3-3 16 0 19" fill="none" stroke="#c8ced8" stroke-width="1.6"/></svg>
          <span>www.meridaleclinic.com</span>
        </li>
      </ul>
      <p class="contact__address">48, Harbor Road, Town, US 10021</p>
    </div>
  </section>

</main>
</body>
</html>
```